zorvan lumet website design

An IT support and IT Security Company - just use dummy text for now for the design. Examples of sites we like the looks and feel of but need it more professional feel are like: www.kelbrovault.uk.com , www.pravok.co.uk, www.quenthardy.com/professional/, www.vur.com, www.melvish.com,

Best to message me if you have any questions

Target Market(s)

small to medium UK based companies that require IT support services

Industry/Entity Type

It Company

Contact Information for Business Card

use dummy name, telephone and email for now, will provide details later.

Logo Text

zorvan lumet (and then below the logo it should say "your IT, networks and security partner")

Coding

Coded - Design and coding required

Number of Pages Required

5+ page

Colors

Designer to choose colors to be used in the design.

Requirements
Must have
• must be professional, yet simple and clear that this is a serious IT support and IT security company.
Nice to have
• 1)The website homepage must have professional quality pictures of IT support or London city skyline or any picture that projects friendly business partners, professionalism and ready to serve.
• 2) Home page needs to include tabs for following pages 'Services' , 'About Us' , 'Contact Us' 'Home'
• 3) Website built customised using wordpress is ideal and easy for us to manage.
• more room for boxed options from homepage (with pic or image in background)
Should not have
• no checkout trolleys or payment options.

```html
<!DOCTYPE html>
<html lang="en">
<head>
<meta charset="utf-8">
<title>Zorvan Lumet — IT Support</title>
<link href="https://fonts.googleapis.com/css2?family=Mulish:wght@400;600;700;800&display=swap" rel="stylesheet">
<style>
:root{
  --blue:#1a8fec;
  --blue-deep:#3f78f5;
  --orange:#ff9f5a;
  --green:#4cdb93;
  --heading:#4b6a9b;
  --text:#6d7f9c;
  --muted:#9aa6b8;
  --band:#f3f5f8;
  --card-border:#dfe3ea;
  --footer:#2f2f31;
  --footer-line:#414145;
  --white:#ffffff;
}
*{margin:0;padding:0;box-sizing:border-box}
html,body{width:1200px;height:2426px;overflow:hidden}
body{font-family:"Mulish",sans-serif;background:var(--white);color:var(--text);position:relative}
.abs{position:absolute}

/* header */
.brand{left:156px;top:22px;font-size:28px;font-weight:800;color:var(--blue);display:flex;align-items:center;gap:10px;white-space:nowrap}
.brand-dot{width:14px;height:14px;background:var(--blue);border-radius:3px}
.nav{left:550px;top:26px;display:flex;gap:6px;align-items:center;font-size:11px;font-weight:600;color:#4a5a72;white-space:nowrap}
.nav a{color:inherit;text-decoration:none;padding:6px 10px}
.nav a.active{background:var(--orange);color:#fff;border-radius:3px;padding:6px 13px}
.login{left:971px;top:26px;width:70px;height:27px;background:var(--blue);color:#fff;border-radius:4px;font-size:11px;font-weight:700;display:flex;align-items:center;justify-content:center}

/* hero */
.hero{left:160px;top:76px;width:880px;height:427px;background:linear-gradient(180deg,#6f6a73 0%,#9a7f6c 35%,#5d4a3e 70%,#3a2f2a 100%)}
.hero-title{left:160px;top:220px;width:880px;text-align:center;color:#fff;font-size:26px;font-weight:700;line-height:31px}
.search{left:352px;top:312px;width:502px;height:58px;background:#fff;border-radius:29px}
.search span{position:absolute;left:36px;top:20px;font-size:12px;color:#b9c0cc}
.search b{position:absolute;right:6px;top:6px;width:144px;height:46px;border-radius:23px;background:var(--orange);color:#fff;font-size:13px;font-weight:700;display:flex;align-items:center;justify-content:center}
.arrow{width:40px;height:40px;border-radius:50%;background:#9ec6f5;top:270px;display:flex;align-items:center;justify-content:center}

/* section titles */
.section-title{left:0;width:1200px;text-align:center;font-size:20px;font-weight:600;color:var(--heading)}

/* industry */
.industry{top:621px;width:255px;height:265px;border-radius:6px;color:#fff;text-align:center;box-shadow:0 4px 10px rgba(0,0,0,.12)}
.industry svg{position:absolute;left:95px;top:40px}
.industry-copy{position:absolute;left:26px;right:26px;top:141px}
.industry h3{font-size:13px;font-weight:700;line-height:16px;margin-bottom:12px}
.industry p{font-size:11.5px;line-height:16px;padding:0 4px}
.btn{color:#fff;font-size:10px;font-weight:700;border-radius:3px;display:flex;align-items:center;justify-content:center;box-shadow:0 3px 6px rgba(0,0,0,.15)}

/* services */
.band{left:0;top:1012px;width:1200px;height:629px;background:var(--band)}
.ghost{font-size:44px;font-weight:700;color:#e9edf3;white-space:nowrap}
.tab-label{top:1139px;font-size:12.5px;font-weight:600;white-space:nowrap}
.service{top:1179px;width:207px;height:398px;background:#fff;border:2px solid var(--card-border);border-top-width:4px;border-radius:7px}
.service h4{position:absolute;left:22px;top:40px;right:18px;font-size:13px;font-weight:700;line-height:16px}
.item{position:absolute;left:22px;right:18px;display:flex;gap:10px;font-size:11px;line-height:16px;color:var(--muted)}
.item em{font-style:normal;font-weight:700;font-size:12px}
.rule{position:absolute;left:14px;right:14px;border-top:1px dashed #c9cfd8}
.service .btn{position:absolute;left:63px;top:336px;width:76px;height:31px}

/* news */
.news-tabs{left:540px;top:1788px;display:flex;gap:24px;font-size:12.5px;font-weight:600}
.news-tabs span{padding:0 0 8px}
.news-tabs .on{color:var(--orange);border-bottom:2px solid var(--orange);padding:0 20px 8px}
.news-box{left:223px;top:1819px;width:752px;height:202px;border:2px solid #edf0f4;border-radius:8px;text-align:center}
.news-box p{margin:26px 28px 0;font-size:11.5px;line-height:19px;color:var(--text)}
.news-box small{display:block;margin-top:14px;font-size:11px}

/* footer */
.footer{left:0;top:2092px;width:1200px;height:334px;background:var(--footer)}
.social{top:2092px;height:58px;width:68px;border-right:1px solid var(--footer-line);display:flex;align-items:center;justify-content:center}
.social i{width:9px;height:9px;border-radius:50%;background:#d8dbe0}
.subscribe{left:673px;top:2102px;width:366px;height:41px;background:#fff;border-radius:21px}
.subscribe span{position:absolute;left:26px;top:13px;font-size:11px;color:#b9c0cc}
.subscribe b{position:absolute;right:4px;top:5px;width:104px;height:31px;border-radius:16px;background:var(--orange);color:#fff;font-size:11.5px;font-weight:700;display:flex;align-items:center;justify-content:center}
.col{top:2186px;width:190px;color:#fff}
.col h5{font-size:19px;font-weight:600;margin-bottom:20px}
.col a{display:block;font-size:10.5px;color:#d6d8dc;text-decoration:none;padding:6px 0;border-bottom:1px solid var(--footer-line)}
.copy{left:160px;top:2387px;font-size:10.5px;color:#8b8d92}
.foot-rule{left:0;top:2369px;width:1200px;border-top:1px solid var(--footer-line)}
</style>
</head>
<body>

<header>
  <div class="abs brand"><span class="brand-dot"></span>zorvan lumet</div>
  <nav class="abs nav">
    <a class="active" href="#">Home</a>
    <a href="#">About Us</a>
    <a href="#">Zorvan Lumet Services</a>
    <a href="#">Blog</a>
    <a href="#">Contact Us</a>
  </nav>
  <div class="abs login">Login</div>
</header>

<section>
  <div class="abs hero" role="img" aria-label="London city skyline at dusk"></div>
  <div class="abs arrow" style="left:64px"><svg width="12" height="12" viewBox="0 0 12 12"><path d="M8 2 L4 6 L8 10" stroke="#fff" stroke-width="2" fill="none"/></svg></div>
  <div class="abs arrow" style="left:1096px"><svg width="12" height="12" viewBox="0 0 12 12"><path d="M4 2 L8 6 L4 10" stroke="#fff" stroke-width="2" fill="none"/></svg></div>
  <h1 class="abs hero-title">Lightning-Fast IT Support Tailored for London<br>Businesses</h1>
  <div class="abs search"><span>Search Your Domain Here</span><b>Search now</b></div>
</section>

<section>
  <h2 class="abs section-title" style="top:553px">IT Support for Your Industry</h2>

  <div class="abs industry" style="left:163px;background:var(--orange)">
    <svg width="66" height="66" viewBox="0 0 66 66" fill="rgba(255,255,255,.35)"><rect x="4" y="44" width="9" height="20"/><rect x="18" y="36" width="9" height="28"/><rect x="32" y="28" width="9" height="36"/><rect x="46" y="18" width="9" height="46"/></svg>
    <div class="industry-copy">
      <h3>IT Support For Financial</h3>
      <p>Ut enim ad minim veniam, quis nostrud exercitation ullamco laboris nisi ut aliquip ex ea.</p>
    </div>
  </div>
  <div class="abs industry" style="left:469px;background:var(--green)">
    <svg width="66" height="66" viewBox="0 0 66 66" fill="rgba(255,255,255,.35)"><rect x="14" y="20" width="22" height="44"/><rect x="38" y="32" width="16" height="32"/><path d="M10 22 L25 8 L40 22Z"/></svg>
    <div class="industry-copy">
      <h3>IT Support for the Property<br>Industry</h3>
      <p>Ut enim ad minim veniam, quis nostrud exercitation.</p>
    </div>
  </div>
  <div class="abs industry" style="left:786px;background:var(--blue-deep)">
    <svg width="66" height="66" viewBox="0 0 66 66" fill="rgba(255,255,255,.7)"><path d="M44 10 L56 22 L26 52 L12 56 L16 42Z"/></svg>
    <div class="industry-copy">
      <h3>IT Support for Professional<br>Services</h3>
      <p>Browse or search the knowledge base for answers to many common questions.</p>
    </div>
  </div>

  <div class="abs btn" style="left:548px;top:925px;width:100px;height:31px;background:var(--blue)">Learn More</div>
</section>

<section>
  <div class="abs band"></div>
  <h2 class="abs section-title" style="top:1062px">Net Security Services</h2>

  <div class="abs ghost" style="left:148px;top:1118px">Service 1</div>
  <div class="abs ghost" style="left:378px;top:1118px">Service 2</div>
  <div class="abs ghost" style="left:612px;top:1118px">Service 3</div>
  <div class="abs ghost" style="left:843px;top:1118px">Service 4</div>
  <div class="abs tab-label" style="left:225px;color:var(--blue-deep)">Quotebridge Terminal</div>
  <div class="abs tab-label" style="left:498px;color:var(--orange)">Email Services</div>
  <div class="abs tab-label" style="left:730px;color:var(--green)">Email Services</div>
  <div class="abs tab-label" style="left:937px;color:var(--blue-deep)">Technical Support</div>

  <div class="abs service" style="left:150px;border-top-color:#c9ced6">
    <h4 style="color:var(--blue-deep)">Quotebridge Terminal</h4>
    <div class="item" style="top:84px"><em style="color:var(--blue-deep)">1</em><span>Lorem ipsum dolor sit amet, consectetur adipiscing elit, sed do eiusmod tempor incididunt ut labore et dolore magna aliqua.</span></div>
    <div class="rule" style="top:178px"></div>
    <div class="item" style="top:206px"><em style="color:var(--blue-deep)">2</em><span>Lorem ipsum dolor sit amet, consectetur adipiscing elit, sed do eiusmod tempor incididunt ut labore et dolore magna aliqua.</span></div>
    <div class="rule" style="top:301px"></div>
    <div class="btn" style="background:var(--blue)">Read More</div>
  </div>
  <div class="abs service" style="left:380px;border-top-color:var(--orange)">
    <h4 style="color:var(--orange)">Execution and Order Management</h4>
    <div class="item" style="top:84px"><em style="color:var(--orange)">1</em><span>Lorem ipsum dolor sit amet, consectetur adipiscing elit, sed do eiusmod tempor incididunt ut labore et dolore magna aliqua.</span></div>
    <div class="rule" style="top:178px"></div>
    <div class="item" style="top:206px"><em style="color:var(--orange)">2</em><span>Lorem ipsum dolor sit amet, consectetur adipiscing elit, sed do eiusmod tempor incididunt ut labore et dolore magna aliqua.</span></div>
    <div class="rule" style="top:301px"></div>
    <div class="btn" style="background:var(--orange)">Read More</div>
  </div>
  <div class="abs service" style="left:613px;border-top-color:var(--green)">
    <h4 style="color:var(--green)">Data and Content</h4>
    <div class="item" style="top:84px"><em style="color:var(--green)">1</em><span>Lorem ipsum dolor sit amet, consectetur adipiscing elit, sed do eiusmod tempor incididunt ut labore et dolore magna aliqua.</span></div>
    <div class="rule" style="top:178px"></div>
    <div class="item" style="top:206px"><em style="color:var(--green)">2</em><span>Lorem ipsum dolor sit amet, consectetur adipiscing elit, sed do eiusmod tempor incididunt ut labore et dolore magna aliqua.</span></div>
    <div class="rule" style="top:301px"></div>
    <div class="btn" style="background:var(--green)">Read More</div>
  </div>
  <div class="abs service" style="left:844px;border-top-color:var(--blue-deep)">
    <h4 style="color:var(--blue-deep)">Financial Data Management</h4>
    <div class="item" style="top:84px"><em style="color:var(--blue-deep)">1</em><span>Lorem ipsum dolor sit amet, consectetur adipiscing elit, sed do eiusmod tempor incididunt ut labore et dolore magna aliqua.</span></div>
    <div class="rule" style="top:178px"></div>
    <div class="item" style="top:206px"><em style="color:var(--blue-deep)">2</em><span>Lorem ipsum dolor sit amet, consectetur adipiscing elit, sed do eiusmod tempor incididunt ut labore et dolore magna aliqua.</span></div>
    <div class="rule" style="top:301px"></div>
    <div class="btn" style="background:var(--blue-deep)">Read More</div>
  </div>
</section>

<section>
  <div class="abs ghost" style="left:585px;top:1678px;color:#eef1f6">News &amp; Blogs</div>
  <h2 class="abs section-title" style="top:1694px">News &amp; Blogs</h2>
  <div class="abs news-tabs"><span class="on">News</span><span style="color:var(--heading)">Blogs</span></div>
  <div class="abs news-box">
    <p>Lorem ipsum dolor sit amet, consectetur adipiscing elit, sed do eiusmod tempor incididunt ut labore et dolore magna aliqua. Ut enim ad minim veniam, quis nostrud exercitation ullamco laboris nisi ut aliquip ex ea commodo consequat. Duis aute irure dolor in reprehenderit in voluptate velit esse cillum dolore eu fugiat nulla pariatur. Excepteur sint occaecat cupidatat non proident, sunt in culpa qui officia deserunt mollit anim id est laborum.</p>
    <small>15 Feb-2018</small>
  </div>
  <div class="abs btn" style="left:561px;top:1963px;width:76px;height:31px;background:var(--orange)">Read More</div>
</section>

<footer>
  <div class="abs footer"></div>
  <div class="abs social" style="left:160px;background:var(--blue);border-right:0"><i style="background:#fff"></i></div>
  <div class="abs social" style="left:228px"><i></i></div>
  <div class="abs social" style="left:296px"><i></i></div>
  <div class="abs social" style="left:364px"><i></i></div>
  <div class="abs social" style="left:432px"><i></i></div>
  <div class="abs social" style="left:500px"><i></i></div>
  <div class="abs subscribe"><span>Enter Your Email Here</span><b>Subscribe</b></div>

  <div class="abs col" style="left:160px"><h5>Resources</h5><a>IT Services Data Sheet</a><a>Managed IT Support Data Sheet</a><a>Business Continuity Checklist</a></div>
  <div class="abs col" style="left:398px"><h5>Services</h5><a>Business Continuity</a><a>IT Support &amp; Field Service</a><a>Outsourced Service Desk</a></div>
  <div class="abs col" style="left:631px"><h5>Useful Links</h5><a>Network &amp; Infrastructure</a><a>Client Testimonials</a><a>Terms of Service</a></div>
  <div class="abs col" style="left:867px"><h5>Contact Us</h5><a>Technical Support</a><a>Contact Us</a><a>System Status</a></div>

  <div class="abs foot-rule"></div>
  <div class="abs copy">© Copyright 2018 Zorvan Lumet., All Right Reserved.</div>
</footer>

</body>
</html>
```